Business Card Design for Varomir Facility Services

We are looking for a Business Card Design for the Company "Varomir Facility Services."
Front side:
- Company Logo (small)
- Company Name, address, pohone, website and personal data.
- white background, for text e.g. company colors (blue or green like in the logo)
Please use following data:
Company data:
Varomir Facility Services Kostelac
Birkenhaldweg 14
8457 Lindenried
www.varomir-fs.ch
Person data:
Tarik Kostelac
Geschäftsführer
+41 76 519 47 83
info@varomir-fs.ch
Back side:
could be colored in blue or green
please use a big logo sing and some smaller icons to say what is all beeing offered in facility services, like cleaning, maintenance cleaning
industrial cleaning, caretaking, gardening, disposal. There is no need for everyone of the icons if there are similar or an icon is standing for more of them.
colors to use:
blue: HEX 246BB0
green: HEX 52B33E

```html
<!DOCTYPE html>
<html lang="de">
<head>
<meta charset="utf-8">
<title>Varomir Facility Services – Visitenkarte</title>
<link rel="stylesheet" href="https://fonts.googleapis.com/css2?family=Poppins:wght@400;500;600&display=swap">
<style>
  :root {
    --brand-blue: #0a51ad;
    --brand-green: #52b33e;
    --card-white: #ffffff;
    --text-grey: #4f4f4f;
    --rule-grey: #8a8a8a;
    --stage: #ebe8e4;
  }
  * { box-sizing: border-box; margin: 0; padding: 0; }
  html, body {
    width: 1125px; height: 1200px; overflow: hidden;
    background: var(--stage);
    font-family: "Poppins", sans-serif;
  }
  .canvas { position: relative; width: 1125px; height: 1200px; }
  .card {
    position: absolute; left: 150px; width: 825px; height: 472px;
    box-shadow: 0 4px 10px rgba(0,0,0,0.25);
  }
  .card--front { top: 98px; background: var(--card-white); }
  .card--back { top: 631px; background: var(--brand-blue); }

  .brand-mark {
    position: absolute; right: 38px; top: 88px;
    display: flex; align-items: center; gap: 14px;
    color: var(--brand-blue); font-weight: 600;
    font-size: 30px; line-height: 1.15; text-align: right;
  }
  .brand-mark__dot {
    width: 26px; height: 26px; border-radius: 50%;
    background: var(--brand-green); flex: none;
  }

  .person { position: absolute; left: 35px; top: 264px; }
  .person__name { color: var(--brand-blue); font-weight: 600; font-size: 31px; line-height: 1.2; }
  .person__role { color: var(--brand-green); font-size: 20px; line-height: 1.2; }
  .rule { position: absolute; left: 35px; right: 38px; top: 336px; border-top: 1px solid var(--rule-grey); }

  .contact { position: absolute; left: 35px; top: 356px; list-style: none; }
  .contact li {
    display: flex; align-items: center; gap: 10px;
    color: var(--text-grey); font-size: 19px; line-height: 26px;
  }
  .contact svg { width: 18px; height: 18px; fill: var(--brand-blue); flex: none; }

  .address {
    position: absolute; right: 38px; top: 358px;
    font-style: normal; text-align: right;
    color: var(--text-grey); font-size: 19px; line-height: 25px;
  }

  .back-mark {
    position: absolute; left: 0; right: 0; top: 160px;
    display: flex; justify-content: center; align-items: center; gap: 22px;
    color: var(--card-white); font-weight: 600; font-size: 44px; line-height: 1.1;
  }
  .back-mark__dot {
    width: 60px; height: 60px; border-radius: 50%;
    background: var(--brand-green); flex: none;
  }
  .services {
    position: absolute; left: 0; right: 0; top: 378px;
    text-align: center; color: var(--card-white);
    font-size: 21px; line-height: 25px;
  }
</style>
</head>
<body>
<main class="canvas">
  <section class="card card--front" aria-label="Vorderseite">
    <div class="brand-mark">
      <span class="brand-mark__dot"></span>
      <span>Varomir<br>Facility Services</span>
    </div>

    <div class="person">
      <p class="person__name">Tarik Kostelac</p>
      <p class="person__role">Geschäftsführer</p>
    </div>
    <div class="rule"></div>

    <ul class="contact">
      <li>
        <svg viewBox="0 0 18 18" aria-hidden="true"><path d="M5 1h8a1.5 1.5 0 0 1 1.5 1.5v13A1.5 1.5 0 0 1 13 17H5a1.5 1.5 0 0 1-1.5-1.5v-13A1.5 1.5 0 0 1 5 1zm.5 2v10h7V3zM9 14a1 1 0 1 0 0 2 1 1 0 0 0 0-2z"/></svg>
        +41 76 519 47 83
      </li>
      <li>
        <svg viewBox="0 0 18 18" aria-hidden="true"><path d="M1 4h16v10H1zm1.5 1.2v.3L9 10l6.5-4.5v-.3zm0 2.1v5.5h13V7.3L9 11.8z"/></svg>
        info@varomir-fs.ch
      </li>
      <li>
        <svg viewBox="0 0 18 18" aria-hidden="true"><path d="M9 1a8 8 0 1 0 0 16A8 8 0 0 0 9 1zm-1 2.6c-.6.8-1.6 1.2-2.3 2 .5.8 1.8.6 2.3 1.4.4.8-.6 1.5 0 2.4.6.8 1.6.5 1.7 1.6.1 1-.6 2-.4 3.2a6 6 0 0 1-6-5.4c.9-.5 1.8-.2 2.2-1.2C4.8 6.3 6 4.3 8 3.6zm4 1.6c.8.5 1.4 1.2 1.8 2-.7.3-1.5 0-2-.6-.3-.4-.1-1 .2-1.4z"/></svg>
        www.varomir-fs.ch
      </li>
    </ul>

    <address class="address">
      Varomir Facility Services Kostelac<br>
      Birkenhaldweg 14<br>
      8457 Lindenried
    </address>
  </section>

  <section class="card card--back" aria-label="Rückseite">
    <div class="back-mark">
      <span class="back-mark__dot"></span>
      <span>Varomir<br>Facility Services</span>
    </div>
    <p class="services">
      Cleaning | Maintenance cleaning | Industrial cleaning<br>
      Caretaking | Gardening | Disposal
    </p>
  </section>
</main>
</body>
</html>
```